Bold, Modern, Clean "Kestrelwaymassage.com" website

Why we stand out?
We are a male and female mobile massage team. Our names are Paul and Lina. 
Kestrel Way is a Seattle based mobile massage service. Our massage is offered to the community with a goal of facilitating balance within each individual. We specialize in integrated Pain management, and sports/medical massage therapy. Every client's first assessment is attended by our male and female massage therapist team. Depending on the goals identified for an individual determines which therapist will be assigned to provide treatment, if not both.

Our passion...
Here at Kestrel Way, we have a great passion for Postural Resoration and how it is integrated into an individual's Massage treatment. We pride ourselves in being natural facilitators of healing, which takes the ego of the therapist out of the client's healing process. We strive to deliver the best massage possible by including modalities such as Neuromuscular, Myofascial release, spontaneous muscle release, postural restoration, orthopedic, and medical massage.

Our education...

We are both Graduates of Venmora, school of massage therapy. We have continuing education in medical massage, myofacial release, trigger point therapy, postural restoration, anatomy, and spontaneous muscle release. Lina is also a Certified Yoga Instructor, which amplifies her experience with flexibility and strength as it pertains to each individual. Paul's passion is Massage, stretching, and strength training to encourage postural restoration and realignment.

Our rates-

Our rates are $75/ 60 minutes, $95/ 90 minutes, and $120/ 120 minutes.

Education-
Both Lina and I worked as behavioral health professionals that specialized in life skills mentoring for youth who had experienced different types of trauma. This led us both to want to help others in a different environment, where individuals can be empowered to take responsibility over their own healing. To us, massage is a type of manipulation physical therapy, that encourages healing on many levels.

Advice to any massage client-
The most important thing to 'us', as Licenced providers is to get you on to our table to show you our skills. But a good therapist never forgets that it's not about what we do for you, but what we can facilitate for you. Your health and healing has nothing to do with us. It is yours, not ours. Identify what your goals are with any Therapist, and know what the end looks like. Progress should be tangible, such as range of motion, and decreased pain.

Lina and Paul at Kestrel Way are awesome! I recently had open heart surgery, and Lina worked on me to increase my range of motion while helping with the pinched nerve from my arm being in the same position for so long during my surgery. My wife drives a lot for work, and Paul has helped decrease her neck and lower back pain immensely. They are seriously the best therapists I have ever worked with. I would recommend them to anyone who needs anything from stress relief to a medical massage treatment. They are professional, up beat, easy going, and always on time. And, I love that they meet us where ever we like! We did a staycation recently, where they came to our hotel to give us relaxation massages. Although usually they come to our home, where we focus on pain related issues. We will continue to work with them for a long, long time.

Target Market(s)

Mobile massage therapy clients

Industry/Entity Type

Massage Therapy

Coding

Coded - Design and coding required

Number of Pages Required

1 page

Font styles to use
Serif
Sans Serif

Requirements
Must have
• Please add or remove any information that would help the presentation of our website. Our logo is posted below, please include into the website.
• Please include a contact field that includes, kestrelwaymassage@fernmail.net,
• (206) 555-0148
• We have also included our own stock photos, as well as a photo of Paul and Lina. Please include a cropped photo of both massage therapists.

```html
<!DOCTYPE html>
<html lang="en">
<head>
<meta charset="utf-8">
<title>Kestrel Way Mobile Massage</title>
<link rel="stylesheet" href="https://fonts.googleapis.com/css2?family=Roboto:wght@300;400;500;700&family=Open+Sans:wght@400;600&family=Pinyon+Script&display=swap">
<style>
:root{
  --nav-bg:#262626;
  --nav-active:#2b3a8f;
  --navy:#1d2f6f;
  --blue:#1a85c4;
  --teal-band:#1684b3;
  --accent-blue:#1a9ad6;
  --dark-overlay:rgba(38,38,38,.78);
  --text-light:#ffffff;
  --text-muted:#8a8a8a;
  --grey-bg:#ececec;
  --contact-bg:#272727;
  --footer-bg:#27306b;
  --btn-dark:#444444;
  --friendwall:#1877e0;
  --chirper:#1da1e6;
  --linkpro:#1f4f66;
  --snapgram:#cc2234;
}
*{margin:0;padding:0;box-sizing:border-box}
html,body{width:1200px;height:2590px;overflow:hidden}
body{position:relative;font-family:"Roboto",Arial,sans-serif;background:#fff;color:#333}
.abs{position:absolute}

/* navigation */
.site-nav{position:absolute;top:0;left:0;width:1200px;height:66px;background:var(--nav-bg);z-index:5;display:flex;align-items:center;padding-left:47px}
.site-nav a{color:var(--text-light);text-decoration:none;font-family:"Open Sans",sans-serif;font-size:12.5px;font-weight:600;text-transform:uppercase;height:66px;line-height:66px;padding:0 16px}
.site-nav a.is-active{background:var(--nav-active)}
.site-nav a+a{margin-left:17px}

/* hero */
.hero{position:absolute;top:0;left:0;width:1200px;height:786px;overflow:hidden}
.hero-photo{position:absolute;inset:0;background:radial-gradient(ellipse at 70% 35%,#8a5a40 0%,#5a3626 45%,#2e1d15 100%)}
.hero-curve{position:absolute;left:0;top:0}
.brand-mark{position:absolute;left:510px;top:68px;width:180px;height:180px;border-radius:50%;background:var(--navy);border:10px solid #333;display:flex;align-items:center;justify-content:center;text-align:center;color:var(--text-light);font-weight:700;font-size:28px;line-height:1.1;text-transform:uppercase}
.hero-title{position:absolute;top:326px;width:1200px;text-align:center;color:var(--text-light);font-weight:400;font-size:66px;letter-spacing:1px}
.hero-lead{position:absolute;top:410px;left:240px;width:720px;text-align:center;color:#e5e5e5;font-size:14.5px;line-height:22px}
.slide-arrow{position:absolute;top:390px;width:38px;height:38px;border-radius:50%;background:rgba(255,255,255,.75)}
.slide-arrow svg{display:block}
.service-thumbs{position:absolute;top:661px;left:0;width:1200px}
.thumb{position:absolute;width:150px;margin-left:-75px;text-align:center}
.thumb-img{width:64px;height:62px;margin:0 auto;border:2px solid #fff;background:linear-gradient(135deg,#e2b898,#a8735a)}
.thumb-label{margin-top:12px;color:var(--text-light);font-size:14px;text-transform:uppercase}
.thumb.is-current .thumb-label{color:var(--accent-blue)}
.hero-shadow{position:absolute;top:786px;left:60px;width:1080px;height:16px;background:radial-gradient(ellipse at center top,rgba(0,0,0,.35),rgba(0,0,0,0) 70%)}

/* intro */
.intro{position:absolute;top:786px;left:0;width:1200px;height:259px;background:#fff}
.intro-title{position:absolute;top:62px;width:1200px;text-align:center;font-size:28px;font-weight:700;color:var(--navy);text-transform:uppercase}
.intro-title span{color:var(--blue)}
.intro-text{position:absolute;top:110px;left:155px;width:890px;text-align:center;font-family:"Open Sans",sans-serif;font-size:11px;line-height:23px;color:var(--text-muted)}

/* specialties */
.specialties{position:absolute;top:1045px;left:0;width:1200px;height:652px;overflow:hidden}
.specialties-photo{position:absolute;inset:0;background:radial-gradient(ellipse at 55% 40%,#6a4a38 0%,#45302a 50%,#2a1f1b 100%)}
.spec-num{position:absolute;left:93px;width:72px;height:72px;border-radius:50%;background:var(--accent-blue);color:#fff;font-size:36px;text-align:center;line-height:72px;font-weight:300}
.spec-title{position:absolute;left:181px;color:#fff;font-size:22px}
.spec-text{position:absolute;left:95px;width:870px;color:#e8e8e8;font-size:12px;line-height:19px}
.spec-divider{position:absolute;left:95px;top:277px;width:846px;height:1px;background:rgba(255,255,255,.55)}
.btn{position:absolute;display:block;color:#fff;text-decoration:none;text-align:center;text-transform:uppercase;font-size:14px}
.btn-view{left:97px;top:476px;width:122px;height:42px;line-height:42px;background:#1387c0}

/* offer band */
.offer-band{position:absolute;top:1697px;left:0;width:1200px;height:152px;background:linear-gradient(90deg,#1a8dbb,#137aa8)}
.offer-title{position:absolute;left:230px;top:40px;font-family:"Pinyon Script",cursive;font-size:44px;color:#fff}
.btn-more{left:870px;top:48px;width:163px;height:51px;line-height:51px;background:var(--footer-bg);font-size:17px;font-weight:500}

/* video */
.video{position:absolute;top:1849px;left:0;width:1200px;height:327px;overflow:hidden}
.video-photo{position:absolute;inset:0;background:linear-gradient(90deg,#1e1714 0%,#3a2820 50%,#2a1c16 100%)}
.video-title{position:absolute;left:214px;top:92px;color:#fff;font-size:33px;font-weight:700;text-transform:uppercase}
.video-text{position:absolute;left:216px;top:150px;width:480px;color:#fff;font-size:16px;line-height:23px}
.btn-learn{left:216px;top:216px;width:153px;height:38px;line-height:38px;background:var(--btn-dark);font-size:15px}
.play{position:absolute;left:784px;top:134px}

/* social */
.social{position:absolute;top:2176px;left:0;width:1200px;height:226px;background:var(--grey-bg)}
.social-title{position:absolute;top:42px;width:1200px;text-align:center;font-size:28px;font-weight:500;color:var(--navy);text-transform:uppercase}
.social-title span{color:var(--blue)}
.social-item{position:absolute;top:115px;width:216px;text-align:center}
.social-btn{display:block;height:50px;line-height:50px;color:#fff;font-size:20px;font-weight:500;text-decoration:none}
.social-count{margin-top:12px;font-size:12px;color:var(--text-muted)}
.friendwall{background:var(--friendwall)}
.chirper{background:var(--chirper)}
.linkpro{background:var(--linkpro)}
.snapgram{background:var(--snapgram)}

/* contact */
.contact-bar{position:absolute;top:2402px;left:0;width:1200px;height:105px;background:var(--contact-bg);color:#fff;font-size:20px}
.contact-icon{position:absolute;top:33px;width:38px;height:38px;border:1px solid #888}
.contact-icon svg{display:block;margin:8px}
.contact-text{position:absolute;top:40px}

/* footer */
.site-footer{position:absolute;top:2507px;left:0;width:1200px;height:83px;background:var(--footer-bg);color:#fff;font-size:11px;text-align:center;line-height:83px;font-family:"Open Sans",sans-serif}
</style>
</head>
<body>

<nav class="site-nav">
  <a class="is-active" href="#">Home</a>
  <a href="#">Why we stand out?</a>
  <a href="#">Our passion</a>
  <a href="#">Education</a>
  <a href="#">Our rates</a>
  <a href="#">5/5 stars massage therapy</a>
  <a href="#">Testimonials</a>
  <a href="#">Contact</a>
</nav>

<header class="hero">
  <div class="hero-photo" role="img" aria-label="Photo of a client receiving a relaxing back massage"></div>
  <svg class="hero-curve" width="1200" height="786" viewBox="0 0 1200 786" aria-hidden="true">
    <path d="M0,770 Q600,400 1200,770 L1200,786 L0,786 Z" fill="rgba(40,40,40,.8)"/>
  </svg>
  <div class="brand-mark">Kestrel<br>Way</div>
  <h1 class="hero-title">REFLEXOLOGY</h1>
  <p class="hero-lead">Lorem ipsum dolor sit amet, consectetur adipiscing elit, sed do eiusmod tempor incididunt ut labore et dolore magna aliqua. Ut enim ad minim veniam, quis nostrud exercitation .</p>
  <div class="slide-arrow" style="left:21px">
    <svg width="38" height="38" viewBox="0 0 38 38"><path d="M22 12 L15 19 L22 26" fill="none" stroke="#444" stroke-width="3"/></svg>
  </div>
  <div class="slide-arrow" style="left:1137px">
    <svg width="38" height="38" viewBox="0 0 38 38"><path d="M16 12 L23 19 L16 26" fill="none" stroke="#444" stroke-width="3"/></svg>
  </div>
  <div class="service-thumbs">
    <div class="thumb is-current" style="left:347px"><div class="thumb-img" role="img" aria-label="Shoulder massage photo"></div><div class="thumb-label">Perspiciatis</div></div>
    <div class="thumb" style="left:499px"><div class="thumb-img" role="img" aria-label="Facial massage photo"></div><div class="thumb-label">Nulla</div></div>
    <div class="thumb" style="left:649px"><div class="thumb-img" role="img" aria-label="Head massage photo"></div><div class="thumb-label">Vestibulum</div></div>
    <div class="thumb" style="left:796px"><div class="thumb-img" role="img" aria-label="Sports therapy photo"></div><div class="thumb-label">Sedutperspi</div></div>
  </div>
</header>
<div class="hero-shadow"></div>

<section class="intro">
  <h2 class="intro-title">Kestrel Way <span>Mobile Massage</span></h2>
  <p class="intro-text">Kestrel Way is a Seattle based mobile massage team that brings care to your home, hotel or office. We focus on integrated pain management and sports and medical massage, and every first visit is attended by both of our therapists so your plan fits your goals. We bring the table, the oils and the time you need, so you can relax and heal where you feel most at ease.</p>
</section>

<section class="specialties">
  <div class="specialties-photo" role="img" aria-label="Photo of a smiling client resting during a massage"></div>
  <div class="spec-num" style="top:129px">1</div>
  <h3 class="spec-title" style="top:149px">Integrated Pain Management</h3>
  <p class="spec-text" style="top:217px">Lorem ipsum dolor sit amet, consectetur adipiscing elit, sed do eiusmod tempor incididunt ut labore et dolore magna aliqua. Ut enim ad minim veniam, quis nostrud exercitation ullamco laboris nisi ut aliquip ex ea commodo consequat.</p>
  <div class="spec-divider"></div>
  <div class="spec-num" style="top:300px">2</div>
  <h3 class="spec-title" style="top:320px">Sports/Medical Massage Therapy</h3>
  <p class="spec-text" style="top:378px">Lorem ipsum dolor sit amet, consectetur adipiscing elit, sed do eiusmod tempor incididunt ut labore et dolore magna aliqua. Ut enim ad minim veniam, quis nostrud exercitation ullamco laboris nisi ut aliquip ex ea commodo consequat.</p>
  <a class="btn btn-view" href="#">View all</a>
</section>

<section class="offer-band">
  <p class="offer-title">The Best Offers For Foot Massage</p>
  <a class="btn btn-more" href="#">More</a>
</section>

<section class="video">
  <div class="video-photo" role="img" aria-label="Photo of a massage session in warm candlelight"></div>
  <h2 class="video-title">Latest Massage Video</h2>
  <p class="video-text">Lorem ipsum dolor sit amet, consectetur adipiscing elit, sed do eiusmod tempor</p>
  <a class="btn btn-learn" href="#">Learn more</a>
  <svg class="play" width="84" height="84" viewBox="0 0 84 84" aria-label="Play video">
    <circle cx="42" cy="42" r="37" fill="rgba(255,255,255,.12)" stroke="#cfcfcf" stroke-width="6"/>
    <path d="M33 26 L60 42 L33 58 Z" fill="#cfcfcf"/>
  </svg>
</section>

<section class="social">
  <h2 class="social-title">Follow us to <span>stay in touch</span></h2>
  <div class="social-item" style="left:78px"><a class="social-btn friendwall" href="#">Friendwall</a><div class="social-count">1234 Like</div></div>
  <div class="social-item" style="left:356px"><a class="social-btn chirper" href="#">Chirper</a><div class="social-count">1234 Followers</div></div>
  <div class="social-item" style="left:627px"><a class="social-btn linkpro" href="#">Linkpro</a><div class="social-count">1234 Followers</div></div>
  <div class="social-item" style="left:893px"><a class="social-btn snapgram" href="#">Snapgram</a><div class="social-count">1234 Followers</div></div>
</section>

<section class="contact-bar">
  <div class="contact-icon" style="left:326px">
    <svg width="20" height="20" viewBox="0 0 20 20" aria-hidden="true"><path d="M4 2 L7 2 L8.5 6 L6.5 7.5 Q8 11 12.5 13.5 L14 11.5 L18 13 L18 16 Q17 18 15 18 Q7 17 2 5 Q2 3 4 2 Z" fill="#fff"/></svg>
  </div>
  <span class="contact-text" style="left:383px">(206) 555-0148</span>
  <div class="contact-icon" style="left:589px">
    <svg width="20" height="20" viewBox="0 0 20 20" aria-hidden="true"><rect x="2" y="4.5" width="16" height="11" fill="none" stroke="#fff" stroke-width="1.6"/><path d="M2 4.5 L10 11 L18 4.5" fill="none" stroke="#fff" stroke-width="1.6"/></svg>
  </div>
  <span class="contact-text" style="left:646px">kestrelwaymassage@fernmail.net</span>
</section>

<footer class="site-footer">All Right Reserved. Copyright ©2015 Company Name</footer>

</body>
</html>
```